Dental Office Needs Exciting New Stationary

We need a stationary design that incorporates the logo that we already have and would like to keep the existing color scheme. We need something clean and professional. This is a Endodontic (root canals) office and must represent a dental specialist's office. I need a design for a business card, envelope, and letterhead that all coordinate. I would like the business card to incorporate the information in the business card sample that I am providing. I made the business card design myself but would like to see a better one.
Dental

```html
<!DOCTYPE html>
<html lang="en">
<head>
<meta charset="utf-8">
<title>Summit Endodontics Stationery</title>
<link rel="stylesheet" href="https://fonts.googleapis.com/css2?family=Montserrat:wght@400;500;600&display=swap">
<style>
  :root {
    --brand-blue: #1a78c2;
    --brand-grey: #a6a8ab;
    --ink: #3a3a3a;
    --paper: #ffffff;
    --backdrop: #9b9b9b;
    --caption: #f2f2f2;
  }
  * { box-sizing: border-box; }
  html, body {
    margin: 0; width: 1200px; height: 640px; overflow: hidden;
    background: var(--backdrop);
    font-family: "Montserrat", sans-serif; color: var(--ink);
  }
  .canvas { position: relative; width: 1200px; height: 640px; }
  .sheet { position: absolute; background: var(--paper); overflow: hidden; box-shadow: 0 2px 6px rgba(0,0,0,.25); }
  .sheet--blue { background: var(--brand-blue); color: var(--paper); }

  /* brand name lockup */
  .wordmark { display: flex; align-items: center; gap: 8px; color: var(--brand-blue); font-weight: 600; letter-spacing: .04em; line-height: 1.05; }
  .wordmark__dot { width: 18px; height: 18px; border-radius: 50%; background: currentColor; flex: none; }
  .wordmark__name { display: flex; flex-direction: column; }
  .wordmark--light { color: var(--paper); }

  /* letterhead */
  .letterhead { left: 30px; top: 30px; width: 360px; height: 466px; }
  .letterhead__wave { position: absolute; left: 0; top: 0; width: 100%; height: 80px; }
  .letterhead .wordmark { position: absolute; right: 24px; top: 52px; font-size: 15px; }
  .letterhead__footer { position: absolute; left: 22px; right: 22px; bottom: 18px; display: flex; gap: 10px; font-size: 6.5px; align-items: flex-start; }
  .letterhead__footer .sig { color: var(--brand-blue); font-weight: 600; font-size: 8px; }
  .letterhead__footer .sig small { display: block; color: var(--brand-grey); font-weight: 400; font-size: 6px; text-align: right; }
  .letterhead__footer .col { border-left: 1px solid var(--brand-grey); padding-left: 8px; line-height: 1.6; }
  .letterhead__bar { position: absolute; left: 0; right: 0; bottom: 0; height: 7px; background: var(--brand-blue); }

  /* business cards */
  .card { width: 240px; height: 137px; }
  .card__name { color: var(--brand-blue); font-weight: 600; font-size: 10px; letter-spacing: .05em; text-align: right; }
  .card__title { font-size: 7px; text-align: right; }
  .card__rule { height: 1px; background: var(--ink); margin: 2px 0; }
  .contacts { list-style: none; margin: 0; padding: 0; font-size: 7px; line-height: 1.55; }
  .contacts li { display: flex; align-items: center; gap: 5px; }
  .icon { width: 8px; height: 8px; fill: var(--brand-blue); flex: none; }
  .sheet--blue .icon { fill: var(--paper); }

  .card--front-a { left: 420px; top: 30px; padding: 14px 16px; }
  .card--front-a .wordmark { font-size: 12px; }
  .card--front-a .card__head { margin-top: 14px; }
  .card--front-a .contacts { margin-top: 2px; }

  .card--front-b { left: 680px; top: 30px; padding: 12px 16px; }
  .card--front-b .wordmark { font-size: 12px; justify-content: center; margin-top: 18px; }

  .card--back-name { left: 940px; top: 30px; padding: 14px 18px 14px 118px; }
  .card--back-name .card__name, .card--back-name .card__title { color: var(--paper); text-align: left; }
  .card--back-name .contacts { margin-top: 26px; font-size: 6.5px; }

  .card--back-white { left: 420px; top: 190px; display: flex; align-items: center; justify-content: center; }
  .card--back-white .wordmark { font-size: 17px; }
  .card--back-blue { left: 680px; top: 190px; display: flex; align-items: center; justify-content: center; }
  .card--back-blue .wordmark { font-size: 17px; }

  /* envelopes */
  .envelope { width: 370px; height: 160px; top: 350px; }
  .envelope--front { left: 420px; }
  .envelope__wave { position: absolute; left: 0; top: 0; width: 100%; height: 50px; }
  .envelope--front .wordmark { position: absolute; left: 18px; top: 52px; font-size: 11px; }
  .envelope__return { position: absolute; left: 44px; top: 82px; font-size: 5.5px; line-height: 1.6; }
  .envelope--back { left: 810px; }
  .envelope__flap { position: absolute; left: 0; top: 0; width: 100%; height: 62px; }
  .envelope__seal { position: absolute; left: 0; right: 0; top: 20px; display: flex; justify-content: center; font-size: 9px; }

  .caption { position: absolute; left: 940px; top: 196px; color: var(--caption); font-size: 14px; line-height: 1.3; font-weight: 400; }
</style>
</head>
<body>
<svg width="0" height="0" style="position:absolute" aria-hidden="true">
  <symbol id="i-phone" viewBox="0 0 10 10"><path d="M2 1h2l1 2.5-1.2 1a5 5 0 0 0 2.7 2.7l1-1.2L10 7v2a1 1 0 0 1-1 1A8.5 8.5 0 0 1 1 2a1 1 0 0 1 1-1z"/></symbol>
  <symbol id="i-fax" viewBox="0 0 10 10"><path d="M2.5 0h5v3h-5zM0 3.5h10v4.5H8V6H2v2H0zM2.5 6.5h5V10h-5z"/></symbol>
  <symbol id="i-web" viewBox="0 0 10 10"><path d="M5 0a5 5 0 1 0 0 10A5 5 0 0 0 5 0zm0 1.2a3.8 3.8 0 1 1 0 7.6 3.8 3.8 0 0 1 0-7.6zM1.5 4.5h7v1h-7zM4.5 1.5h1v7h-1z"/></symbol>
  <symbol id="i-pin" viewBox="0 0 10 10"><path d="M5 0a3.6 3.6 0 0 0-3.6 3.6C1.4 6.3 5 10 5 10s3.6-3.7 3.6-6.4A3.6 3.6 0 0 0 5 0zm0 2.2a1.4 1.4 0 1 1 0 2.8 1.4 1.4 0 0 1 0-2.8z"/></symbol>
</svg>

<main class="canvas">

  <!-- Letterhead -->
  <section class="sheet letterhead">
    <svg class="letterhead__wave" viewBox="0 0 360 80" preserveAspectRatio="none" aria-hidden="true">
      <path d="M0 0H360V24C250 22 170 44 0 38Z" fill="var(--brand-blue)"/>
      <path d="M0 48C140 50 240 30 360 26V33C240 38 150 62 0 62Z" fill="var(--brand-grey)"/>
    </svg>
    <div class="wordmark"><span class="wordmark__dot"></span><span class="wordmark__name"><span>SUMMIT</span><span>ENDODONTICS</span></span></div>
    <footer class="letterhead__footer">
      <div class="sig">DANIEL R MERCER<small>DDS MS</small></div>
      <div class="col">555.210.4477<br>555.210.4490</div>
      <div class="col">www.summitendo.com<br>480 Alder Avenue, Riverton, CA 95820</div>
    </footer>
    <div class="letterhead__bar"></div>
  </section>

  <!-- Business card front, version A -->
  <section class="sheet card card--front-a">
    <div class="wordmark"><span class="wordmark__dot"></span><span class="wordmark__name"><span>SUMMIT</span><span>ENDODONTICS</span></span></div>
    <div class="card__head">
      <div class="card__name">DANIEL R MERCER</div>
      <div class="card__rule"></div>
      <div class="card__title">DDS MS</div>
    </div>
    <ul class="contacts">
      <li><svg class="icon"><use href="#i-phone"/></svg>555.210.4477</li>
      <li><svg class="icon"><use href="#i-fax"/></svg>555.210.4490</li>
      <li><svg class="icon"><use href="#i-web"/></svg>www.summitendo.com</li>
      <li><svg class="icon"><use href="#i-pin"/></svg>480 Alder Avenue, Riverton, CA 95820</li>
    </ul>
  </section>

  <!-- Business card front, version B -->
  <section class="sheet card card--front-b">
    <div class="card__name">DANIEL R MERCER</div>
    <div class="card__rule"></div>
    <div class="card__title">DDS MS</div>
    <ul class="contacts">
      <li><svg class="icon"><use href="#i-phone"/></svg>555.210.4477</li>
      <li><svg class="icon"><use href="#i-fax"/></svg>555.210.4490</li>
      <li><svg class="icon"><use href="#i-web"/></svg>www.summitendo.com</li>
      <li><svg class="icon"><use href="#i-pin"/></svg>480 Alder Avenue, Riverton, CA 95820</li>
    </ul>
    <div class="wordmark"><span class="wordmark__dot"></span><span class="wordmark__name"><span>SUMMIT</span><span>ENDODONTICS</span></span></div>
  </section>

  <!-- Business card back, blue with contact -->
  <section class="sheet sheet--blue card card--back-name">
    <div class="card__name">DANIEL R MERCER</div>
    <div class="card__title">DDS MS</div>
    <ul class="contacts">
      <li><svg class="icon"><use href="#i-phone"/></svg>555.210.4477</li>
      <li><svg class="icon"><use href="#i-fax"/></svg>555.210.4490</li>
      <li><svg class="icon"><use href="#i-web"/></svg>www.summitendo.com</li>
      <li><svg class="icon"><use href="#i-pin"/></svg>480 Alder Ave, Riverton, CA 95820</li>
    </ul>
  </section>

  <!-- Business card back, white -->
  <section class="sheet card card--back-white">
    <div class="wordmark"><span class="wordmark__dot"></span><span class="wordmark__name"><span>SUMMIT</span><span>ENDODONTICS</span></span></div>
  </section>

  <!-- Business card back, blue -->
  <section class="sheet sheet--blue card card--back-blue">
    <div class="wordmark wordmark--light"><span class="wordmark__dot"></span><span class="wordmark__name"><span>SUMMIT</span><span>ENDODONTICS</span></span></div>
  </section>

  <p class="caption">Letterhead<br>Business Card 2 front 3 back<br>Envelope front and Back</p>

  <!-- Envelope front -->
  <section class="sheet envelope envelope--front">
    <svg class="envelope__wave" viewBox="0 0 370 50" preserveAspectRatio="none" aria-hidden="true">
      <path d="M0 0H370V30C260 24 170 20 0 16Z" fill="var(--brand-blue)"/>
      <path d="M0 22C150 24 260 30 370 36V41C260 36 150 32 0 30Z" fill="var(--brand-grey)"/>
    </svg>
    <div class="wordmark"><span class="wordmark__dot"></span><span class="wordmark__name"><span>SUMMIT</span><span>ENDODONTICS</span></span></div>
    <div class="envelope__return">www.summitendo.com<br>480 Alder Avenue, Riverton, CA 95820</div>
  </section>

  <!-- Envelope back -->
  <section class="sheet envelope envelope--back">
    <svg class="envelope__flap" viewBox="0 0 370 62" preserveAspectRatio="none" aria-hidden="true">
      <path d="M0 0H370V34Q370 60 344 60H36Q14 60 8 40Z" fill="var(--brand-blue)"/>
    </svg>
    <div class="envelope__seal"><div class="wordmark wordmark--light"><span>SUMMIT ENDODONTICS</span></div></div>
  </section>

</main>
</body>
</html>
```